Create a wordpress website for Tovarin business solution

This project is to create a complete website with all pages.

Overview
The purpose of this project is to create a full complete website with all pages (16 pages). The site should be professional and modern. The site is for an IT recruiting and IT training company. The site needs to be easy to administer and update content. It should be simple to add pages, videos and testimonials later. I will leave the site layout, color schemes and flow to the designers.

Navigation Menu (Home, who we are, what we do, what makes us different, why it matters, candidate portal, contact us, Blog)

WHO WE ARE should be a drop down menu with link to pages (about us, mission, vision and purpose, our team)

WHAT WE DO should be drop down menu with link to the following pages (IT Recruiting, IT Training, Hardware and software sales)

What makes us different should be single page with different paragraph titles. (We live what we do, we don't compromise quality, we share knowledge, staffing guarantee)

Why it matters should be single page with paragraph titles. (Quickly fill positions, candidate career development)

Candidate portal should links to my portal login page. I can add the correct URL later. I just need it to link to somewhere. I can change it.

Contact us should have (address, phone number, google map and a form to submit request for a call back)

Blog - This link should launch a wordpress blogging module

Target Market(s)

IT RECRUITING AND CONSULTING

Industry/Entity Type

It Company

Coding

Coded - Design and coding required

Requirements
Must have
• Company Logo
• Navigation Menu (Home, who we are, what we do, what makes us different, why it matters, candidate portal, contact us)
• WHO WE ARE should be a drop down menu with link to pages (about us, mission, vision and purpose, our team)
• WHAT WE DO should be drop down menu with link to the following pages (IT Recruiting, IT Training, Hardware and software sales)
• What makes us different should be single page with different paragraph titles. (We live what we do, we don't compromise quality, we share knowledge, staffing guarantee)
• Why it matters should be single page with paragraph titles. (Quickly fill positions, candidate career development)
• Candidate portal should links to my portal login page. I can add the correct URL later. I just need it to link to somewhere. I can change it.
• Contact us should have (address, phone number, google map and a form to submit request for a call back)

```html
<!DOCTYPE html>
<html lang="en">
<head>
<meta charset="utf-8">
<title>Tovarin Business Solution</title>
<link rel="stylesheet" href="https://fonts.googleapis.com/css2?family=Montserrat:wght@400;500;600&family=Open+Sans:wght@400;600&display=swap">
<style>
:root{
  --blue:#0b5aa5;
  --orange:#e2791b;
  --brown:#8a4a10;
  --dark:#262626;
  --grey-band:#f3f3f3;
  --text:#333;
  --muted:#8a8a8a;
  --line:#cfcfcf;
  --white:#fff;
}
*{box-sizing:border-box;margin:0;padding:0}
html,body{width:1200px;height:2719px;overflow:hidden;background:var(--white)}
body{position:relative;font-family:"Open Sans",Arial,sans-serif;color:var(--text)}
.abs{position:absolute}
h1,h2,h3,.nav a,.btn{font-family:"Montserrat",Arial,sans-serif}

/* header */
.brand{left:0;top:30px;width:1200px;text-align:center;font-family:"Montserrat",Arial,sans-serif;font-weight:600;font-size:38px;color:var(--blue);letter-spacing:1px}
.brand small{display:block;font-size:13px;letter-spacing:3px;margin-top:2px}
.nav{left:0;top:118px;width:1200px;height:38px;background:var(--blue);display:flex;padding-left:132px}
.nav a{color:var(--white);text-decoration:none;font-size:13px;font-weight:500;padding:0 17px;line-height:38px;white-space:nowrap}
.nav a.active{background:var(--orange);padding:0 23px}

/* hero */
.hero{left:0;top:156px;width:1200px;height:457px;background:linear-gradient(100deg,#6d6a64 0%,#b9b6ae 35%,#e4e2dd 60%,#9c948a 100%)}
.hero-title{left:0;top:228px;width:1200px;text-align:center;font-size:25px;font-weight:400;color:#3a3a3a;line-height:32px}
.btn{display:block;border:1px solid #9a9a9a;background:var(--white);color:#444;font-size:13px;text-align:center}
.hero-btn{left:548px;top:303px;width:104px;height:41px;line-height:39px;background:rgba(255,255,255,.85)}
.arrow{top:368px;width:20px;height:32px;background:#333;display:flex;align-items:center;justify-content:center}

/* welcome */
.welcome-img{left:132px;top:680px;width:446px;height:250px;background:linear-gradient(135deg,#b07a45,#d9a86e 50%,#8c5a2c)}
.welcome-title{left:604px;top:672px;font-size:25px;font-weight:500;color:var(--orange)}
.welcome-text{left:604px;top:714px;width:464px;font-size:11.5px;line-height:20.5px;color:var(--muted);text-align:justify}
.read-btn{left:604px;top:890px;width:94px;height:40px;line-height:38px;font-size:11px;color:var(--muted);border-color:var(--line)}

/* what we do */
.band{left:0;width:1200px;background:var(--grey-band)}
.section-title{left:0;width:1200px;text-align:center;font-size:24px;font-weight:500;color:var(--brown)}
.service{left:132px;width:936px;height:95px;background:var(--white);box-shadow:0 1px 4px rgba(0,0,0,.12)}
.service svg{position:absolute;left:14px;top:18px}
.service h3{position:absolute;left:118px;top:14px;font-size:22px;font-weight:500;color:var(--orange)}
.service p{position:absolute;left:118px;top:46px;width:800px;font-size:10.5px;line-height:17px;color:var(--muted)}
.service p a{color:var(--blue);text-decoration:none}

/* blog */
.blog-nav{top:1569px;width:22px;height:22px;border:1px solid #aaa;display:flex;align-items:center;justify-content:center}
.post-img{top:1617px;width:300px;height:191px}
.post-title{top:1822px;width:300px;font-size:14.5px;line-height:21px;color:#333}
.post-text{top:1872px;width:300px;font-size:10.5px;line-height:16px;color:var(--muted)}
.post-btn{top:1940px;width:82px;height:36px;line-height:34px;font-size:10.5px;color:var(--muted);border-color:var(--line)}

/* candidate portal */
.portal-text{left:130px;top:2150px;width:940px;text-align:center;font-size:10.5px;line-height:16px;color:var(--muted)}
.apply-btn{left:548px;top:2199px;width:104px;height:40px;line-height:38px;font-size:13px}

/* contact */
.contact-dark{left:0;top:2302px;width:600px;height:320px;background:var(--dark)}
.contact-orange{left:600px;top:2302px;width:600px;height:320px;background:var(--orange)}
.contact-title{top:2338px;font-family:"Montserrat",Arial,sans-serif;font-size:24px;font-weight:500;color:var(--white)}
.info{left:134px;font-size:11.5px;color:#cfcfcf;display:flex;align-items:center;gap:16px}
.field{height:38px;background:var(--white);font-size:11px;color:#777;padding:0 15px;line-height:38px}
.submit{left:635px;top:2545px;width:85px;height:40px;background:var(--dark);color:var(--white);font-family:"Montserrat",Arial,sans-serif;font-size:12px;font-weight:600;text-align:center;line-height:40px}
.clear{left:734px;top:2557px;font-size:11px;color:var(--dark);text-decoration:underline}

/* footer */
.foot-links{left:132px;top:2650px;font-size:10.5px;color:#555}
.foot-links span{margin:0 6px;color:#999}
.copy{left:132px;top:2676px;font-size:10.5px;color:#555}
.social{top:2657px;width:26px;height:26px;border-radius:50%;background:var(--blue)}
</style>
</head>
<body>

<header>
  <div class="abs brand">Tovarin<small>BUSINESS SOLUTION LLC</small></div>
  <nav class="abs nav">
    <a class="active" href="#">Home</a>
    <a href="#">Who we are</a>
    <a href="#">What we do</a>
    <a href="#">What makes us different</a>
    <a href="#">Why it matters</a>
    <a href="#">Candidate portal</a>
    <a href="#">Contact us</a>
    <a href="#">Blog</a>
  </nav>
</header>

<section>
  <div class="abs hero" role="img" aria-label="Trainer presenting at a whiteboard to a seated group in a bright training room"></div>
  <h1 class="abs hero-title">We are IT recruiting and<br>IT training company</h1>
  <a class="abs btn hero-btn" href="#">Learn More</a>
  <div class="abs arrow" style="left:0"><svg width="8" height="12"><path d="M7 1 2 6l5 5" stroke="#fff" stroke-width="2" fill="none"/></svg></div>
  <div class="abs arrow" style="left:1180px"><svg width="8" height="12"><path d="M1 1l5 5-5 5" stroke="#fff" stroke-width="2" fill="none"/></svg></div>
</section>

<section>
  <div class="abs welcome-img" role="img" aria-label="Handshake over a desk with signed contract papers"></div>
  <h2 class="abs welcome-title">Welcome to Tovarin Business Solution</h2>
  <p class="abs welcome-text">Maecenas rutrum orci vitae nulla egestas fringilla. Vestibulum ante ipsum primis in faucibus orci luctus et ultrices posuere cubilia Curae; Morbi nisi odio, vestibulum sed purus finibus, imperdiet tempus nibh. Vestibulum fermentum id mauris at rhoncus. Maecenas gravida augue nibh, sit amet finibus nisi egestas ut. Nullam sed metus cursus urna varius vulputate. Praesent mollis auctor velit at pellentesque. Pellentesque habitant morbi tristique senectus et netus et malesuada fames ac turpis egestas. Vestibulum ante ipsum primis in faucibus orci luctus et ultrices posuere cubilia Curae; Interdum et malesuada fames ac ante ipsum primis in faucibus.</p>
  <a class="abs btn read-btn" href="#">READ MORE</a>
</section>

<section>
  <div class="abs band" style="top:993px;height:497px"></div>
  <h2 class="abs section-title" style="top:1052px">What We Do</h2>

  <div class="abs service" style="top:1108px">
    <svg width="80" height="60" viewBox="0 0 80 60"><circle cx="46" cy="16" r="11" fill="#555"/><path d="M28 58c0-16 8-24 18-24s18 8 18 24z" fill="#555"/><circle cx="28" cy="18" r="10" fill="#777"/><path d="M10 58c0-15 8-22 18-22s18 7 18 22z" fill="#777"/></svg>
    <h3>IT Recruiting</h3>
    <p>Cras ullamcorper purus eu lacinia mattis. Pellentesque suscipit sapien eu augue ultricies suscipit. Morbi pellentesque malesuada hendrerit. Morbi nulla libero, aliquam non dui sed, laoreet faucibus ipsum. Sed maximus elit mauris, a blandit mi pharetra eu. Nam imperdiet justo et feugiat egestas. <a href="#">Read more</a></p>
  </div>

  <div class="abs service" style="top:1220px">
    <svg width="80" height="60" viewBox="0 0 80 60"><rect x="16" y="8" width="46" height="46" fill="none" stroke="#555" stroke-width="5"/><path d="M32 42l4-12 24-24 8 8-24 24z" fill="#555" stroke="#fff" stroke-width="2"/></svg>
    <h3>IT Training</h3>
    <p>Cras ullamcorper purus eu lacinia mattis. Pellentesque suscipit sapien eu augue ultricies suscipit. Morbi pellentesque malesuada hendrerit. Morbi nulla libero, aliquam non dui sed, laoreet faucibus ipsum. Sed maximus elit mauris, a blandit mi pharetra eu. Nam imperdiet justo et feugiat egestas. <a href="#">Read more</a></p>
  </div>

  <div class="abs service" style="top:1332px">
    <svg width="80" height="60" viewBox="0 0 80 60"><rect x="12" y="10" width="58" height="36" fill="none" stroke="#555" stroke-width="4"/><rect x="4" y="48" width="74" height="5" fill="#555"/><circle cx="36" cy="28" r="5" fill="none" stroke="#555" stroke-width="3"/><circle cx="48" cy="23" r="3" fill="none" stroke="#555" stroke-width="2"/></svg>
    <h3>Hardware and Software Sales</h3>
    <p>Cras ullamcorper purus eu lacinia mattis. Pellentesque suscipit sapien eu augue ultricies suscipit. Morbi pellentesque malesuada hendrerit. Morbi nulla libero, aliquam non dui sed, laoreet faucibus ipsum. Sed maximus elit mauris, a blandit mi pharetra eu. Nam imperdiet justo et feugiat egestas. <a href="#">Read more</a></p>
  </div>
</section>

<section>
  <h2 class="abs section-title" style="top:1563px;color:#333">Blog</h2>
  <div class="abs blog-nav" style="left:534px"><svg width="8" height="10"><path d="M6 1 2 5l4 4" stroke="#777" stroke-width="1.5" fill="none"/></svg></div>
  <div class="abs blog-nav" style="left:644px"><svg width="8" height="10"><path d="M2 1l4 4-4 4" stroke="#777" stroke-width="1.5" fill="none"/></svg></div>

  <div class="abs post-img" style="left:132px;background:linear-gradient(135deg,#6b5a4a,#a88a6c 50%,#3f4a5a)" role="img" aria-label="Group of people seated on a bench using laptops and phones"></div>
  <h3 class="abs post-title" style="left:132px;font-family:'Open Sans',Arial,sans-serif;font-weight:400">Aliquam lacinia dapibus nisi, in ullamcorper est aliquet</h3>
  <p class="abs post-text" style="left:132px">Cras quis efficitur est. Nulla facilisi. Etiam nec lectus dignissim, lacinia leo nec, tincidunt nisi. Mauris sit amet ante eu dolor vestibulum finibus. Nulla ultrices vehicula efficitur.</p>
  <a class="abs btn post-btn" style="left:132px" href="#">Read more</a>

  <div class="abs post-img" style="left:451px;background:linear-gradient(135deg,#f4ead8,#d8b98a 55%,#8a6a44)" role="img" aria-label="Laptop on a desk in warm light"></div>
  <h3 class="abs post-title" style="left:451px;font-family:'Open Sans',Arial,sans-serif;font-weight:400">Mauris finibus velit metus, et auctor sem fringilla semper</h3>
  <p class="abs post-text" style="left:451px">Cras quis efficitur est. Nulla facilisi. Etiam nec lectus dignissim, lacinia leo nec, tincidunt nisi. Mauris sit amet ante eu dolor vestibulum finibus. Nulla ultrices vehicula efficitur.</p>
  <a class="abs btn post-btn" style="left:451px" href="#">Read more</a>

  <div class="abs post-img" style="left:769px;background:linear-gradient(135deg,#dfe3e6,#aab2b8 50%,#5c646a)" role="img" aria-label="Team meeting around a table in a bright office"></div>
  <h3 class="abs post-title" style="left:769px;font-family:'Open Sans',Arial,sans-serif;font-weight:400">Aenean facilisis gravida dui ut commodo elementum nunc.</h3>
  <p class="abs post-text" style="left:769px">Cras quis efficitur est. Nulla facilisi. Etiam nec lectus dignissim, lacinia leo nec, tincidunt nisi. Mauris sit amet ante eu dolor vestibulum finibus. Nulla ultrices vehicula efficitur.</p>
  <a class="abs btn post-btn" style="left:769px" href="#">Read more</a>
</section>

<section>
  <div class="abs band" style="top:2056px;height:246px"></div>
  <h2 class="abs section-title" style="top:2114px">Candidate portal</h2>
  <p class="abs portal-text">Maecenas rutrum orci vitae nulla egestas fringilla. Vestibulum ante ipsum primis in faucibus orci luctus et ultrices posuere cubilia Curae; Morbi nisi odio, vestibulum sed purus finibus, imperdiet tempus nibh. Vestibulum fermentum id mauris at rhoncus. Maecenas gravida augue nibh, sit amet finibus</p>
  <a class="abs btn apply-btn" href="#">Apply Now</a>
</section>

<section>
  <div class="abs contact-dark"></div>
  <div class="abs contact-orange"></div>

  <h2 class="abs contact-title" style="left:134px">Contact Info</h2>
  <div class="abs info" style="top:2389px"><svg width="8" height="11"><path d="M4 11C1 7 0 5 0 4a4 4 0 0 1 8 0c0 1-1 3-4 7z" fill="#ccc"/></svg>24 Building name, Street name, City - Zipcode</div>
  <div class="abs info" style="top:2429px"><svg width="8" height="11"><rect x="1" y="0" width="6" height="11" rx="1" fill="#ccc"/></svg>Phone: 555 010 2847</div>
  <div class="abs info" style="top:2469px"><svg width="10" height="8"><rect width="10" height="8" fill="#ccc"/><path d="M0 0l5 4 5-4" stroke="#262626" fill="none"/></svg>Email: info@tovarinbusinesssolution.com</div>

  <h2 class="abs contact-title" style="left:635px">Request for a call back</h2>
  <div class="abs field" style="left:635px;top:2379px;width:208px">Name *</div>
  <div class="abs field" style="left:859px;top:2379px;width:209px">Email *</div>
  <div class="abs field" style="left:635px;top:2435px;width:208px">Phone</div>
  <div class="abs field" style="left:859px;top:2435px;width:209px">Service Type<svg style="position:absolute;right:14px;top:16px" width="9" height="6"><path d="M1 1l3.5 3.5L8 1" stroke="#777" fill="none"/></svg></div>
  <div class="abs field" style="left:635px;top:2489px;width:433px;height:40px">Decription</div>
  <div class="abs submit">SUBMIT</div>
  <a class="abs clear" href="#">Clear All</a>
</section>

<footer>
  <div class="abs foot-links">Home<span>|</span>Who we are<span>|</span>What we do<span>|</span>What makes us different<span>|</span>Why it matters<span>|</span>Candidate portal<span>|</span>Contact us<span>|</span>Blog</div>
  <div class="abs copy">Copyright &copy; 2016 Company name. All rights reserved.</div>
  <div class="abs social" style="left:975px"></div>
  <div class="abs social" style="left:1006px"></div>
  <div class="abs social" style="left:1038px"></div>
</footer>

</body>
</html>
```